Brightfen Business Card Redesign & Logo Update

We need to update our business cards to something more modern and fresh. Brightfen can provide the current color schemes and old design examples, but welcome creativity in helping us with this redesign. PLEASE NOTE that we no longer utilize the "tree" and/or "leaf" imagery in our branding. If able would apprecaite an update on the quality of our "words only" logo in Ai. / PNG formats too.

Target Market(s)

Investors, landowners, corporate partners, contractors

Industry/Entity Type

Environmental Restoration & Conservation

Contact Information for Business Card

Logo, persons name, title, mailing address, phone and email, website url

Font styles to use
Other font styles liked:
• Merriweather

Requirements
Nice to have
• Logo, persons name, title, mailing address, phone and email, website url, but open to ideams
Should not have
• No all back backgrounds

```html
<!DOCTYPE html>
<html lang="en">
<head>
<meta charset="utf-8">
<title>Brightfen Business Card</title>
<link href="https://fonts.googleapis.com/css2?family=Merriweather:wght@400;700&display=swap" rel="stylesheet">
<style>
  :root {
    --green: #167c3f;
    --orange: #ea7d22;
    --ink: #1c1c1c;
    --paper: #ffffff;
    --backdrop: #e4e5e7;
  }
  * { margin: 0; padding: 0; box-sizing: border-box; }
  html, body { width: 1200px; height: 1000px; overflow: hidden; }
  body {
    background: var(--backdrop);
    font-family: "Merriweather", Georgia, serif;
    color: var(--ink);
    position: relative;
  }
  .card {
    position: absolute;
    top: 357px;
    width: 500px;
    height: 286px;
    background: var(--paper);
    box-shadow: 0 6px 18px rgba(0,0,0,.18);
    overflow: hidden;
  }
  .card--front { left: 70px; }
  .card--back { left: 630px; }

  .wordmark {
    font-weight: 700;
    color: var(--green);
    letter-spacing: 1px;
    text-transform: uppercase;
    line-height: 1;
    white-space: nowrap;
  }
  .card--front .wordmark {
    position: absolute;
    left: 150px; top: 48px;
    font-size: 38px;
  }

  .holder {
    position: absolute;
    right: 290px; top: 128px;
    text-align: right;
  }
  .holder__name {
    font-size: 16px; font-weight: 700;
    color: var(--orange);
    text-transform: uppercase;
    white-space: nowrap;
  }
  .holder__name span { color: var(--green); }
  .holder__title { font-size: 13px; margin-top: 4px; }

  .divider {
    position: absolute;
    left: 220px; top: 118px;
    width: 1.5px; height: 66px;
    background: var(--green);
  }

  .contact {
    position: absolute;
    left: 232px; top: 114px;
    list-style: none;
    font-size: 12px;
    line-height: 1.5;
    white-space: nowrap;
  }
  .contact li { display: flex; align-items: center; gap: 6px; }
  .contact svg { width: 11px; height: 11px; fill: var(--green); flex: none; }

  .address {
    position: absolute;
    left: 40px; top: 204px;
    font-size: 13px;
    white-space: nowrap;
  }

  .bands { position: absolute; left: 0; bottom: 0; width: 500px; height: 60px; }

  .card--back .mark {
    position: absolute;
    left: 50%; top: 50%;
    transform: translate(-50%, -50%);
    display: flex; align-items: center; gap: 14px;
  }
  .mark__dot { width: 30px; height: 30px; border-radius: 50%; background: var(--orange); flex: none; }
  .card--back .wordmark { font-size: 44px; }
</style>
</head>
<body>

<section class="card card--front" aria-label="Business card front">
  <div class="wordmark">Brightfen</div>

  <div class="holder">
    <div class="holder__name">Owen <span>Hale</span></div>
    <div class="holder__title">Founder</div>
  </div>

  <div class="divider"></div>

  <ul class="contact">
    <li><svg viewBox="0 0 24 24"><path d="M6.6 10.8a15 15 0 0 0 6.6 6.6l2.2-2.2a1 1 0 0 1 1-.25 11.4 11.4 0 0 0 3.6.57 1 1 0 0 1 1 1V20a1 1 0 0 1-1 1A17 17 0 0 1 3 4a1 1 0 0 1 1-1h3.5a1 1 0 0 1 1 1c0 1.25.2 2.45.57 3.57a1 1 0 0 1-.25 1z"/></svg>(555) 014-2290</li>
    <li><svg viewBox="0 0 24 24"><path d="M2 6h20v12H2z"/><path d="M2 6l10 7 10-7" fill="none" stroke="#fff" stroke-width="2"/></svg>hello@brightfen.com</li>
    <li><svg viewBox="0 0 24 24"><circle cx="12" cy="12" r="10"/></svg>www.brightfen.com</li>
  </ul>

  <p class="address">48 Reedbank Road, Unit 7, Fenbrook 20917</p>

  <svg class="bands" viewBox="0 0 500 60" aria-hidden="true">
    <polygon points="0,32 232,32 224,60 0,60" fill="var(--green)"/>
    <polygon points="240,20 500,0 500,60 232,60" fill="var(--orange)"/>
  </svg>
</section>

<section class="card card--back" aria-label="Business card back">
  <div class="mark">
    <div class="mark__dot"></div>
    <div class="wordmark">Brightfen</div>
  </div>
</section>

</body>
</html>
```